Business Card Design for company

We want new business cards. We'd like something different-- yet still highly professional. Our tagline is Providing leadership, delivering success. Stock photos are ok, as long as they are relevant and look upscale.

Target Market(s)

Architecture/Business Management Consulting/Engineering Consulting

Contact Information for Business Card

dark gray background with pops of blue might be good, but you tell me. You're the designers. Rounded corners might be nice, but again, you tell me.

Font styles to use
Serif
Sans Serif

Colors
3276b5
5c5c5c
9d9d9d
fbfbfb

Requirements
Nice to have
• Something different, but still very professional.

```html
<!DOCTYPE html>
<html lang="en">
<head>
<meta charset="utf-8">
<title>Norvale International – Business Card</title>
<link href="https://fonts.googleapis.com/css2?family=Open+Sans:wght@400;600&display=swap" rel="stylesheet">
<style>
  :root {
    --page: #e9e9e9;
    --card: #ffffff;
    --blue: #3276b5;
    --blue-light: #6fa9cc;
    --grey: #5c5c5c;
    --grey-soft: #9d9d9d;
    --ink: #1e1e1e;
  }
  html, body {
    margin: 0;
    width: 1200px;
    height: 1023px;
    overflow: hidden;
    background: var(--page);
    font-family: "Open Sans", sans-serif;
  }
  .card {
    position: absolute;
    left: 100px;
    top: 226px;
    width: 1000px;
    height: 571px;
    background: var(--card);
    box-shadow: 0 6px 24px rgba(0,0,0,0.18);
  }
  .band {
    position: absolute;
    left: 0;
    top: 150px;
    width: 100%;
    height: 60px;
    background: linear-gradient(90deg, var(--blue) 0%, var(--blue) 25%, var(--blue-light) 50%, var(--blue) 80%, var(--blue) 100%);
  }
  .holder {
    position: absolute;
    left: 58px;
    top: 52px;
  }
  .holder-name {
    margin: 0;
    font-size: 32px;
    font-weight: 400;
    color: var(--blue);
    line-height: 1.1;
  }
  .holder-role {
    margin: 2px 0 0;
    font-size: 21px;
    color: var(--ink);
  }
  .contact {
    position: absolute;
    left: 320px;
    top: 268px;
    margin: 0;
    padding: 0;
    list-style: none;
    font-size: 22px;
    color: var(--ink);
    line-height: 30px;
  }
  .contact li {
    display: flex;
    align-items: flex-start;
    gap: 12px;
    margin-bottom: 4px;
  }
  .contact svg {
    flex: none;
    width: 20px;
    height: 20px;
    margin-top: 6px;
  }
  .brand {
    position: absolute;
    left: 640px;
    top: 250px;
    display: flex;
    align-items: center;
    gap: 16px;
  }
  .brand-mark {
    width: 22px;
    height: 22px;
    background: var(--blue);
  }
  .brand-name {
    margin: 0;
    font-size: 48px;
    font-weight: 600;
    color: var(--grey);
    line-height: 1.05;
    letter-spacing: 1px;
  }
</style>
</head>
<body>
  <div class="card">
    <div class="band"></div>

    <div class="holder">
      <p class="holder-name">Avery Lund</p>
      <p class="holder-role">Owner</p>
    </div>

    <ul class="contact">
      <li>
        <svg viewBox="0 0 20 20" aria-hidden="true"><rect width="20" height="20" rx="3" fill="#6fa9cc"/><path d="M6 5c1 0 2 2 2 2.5S7 9 7 9c.6 1.6 2.4 3.4 4 4 0 0 .8-1 1.5-1S15 13 15 14s-1.5 1.5-2 1.5C9 15.5 4.5 11 4.5 7 4.5 6 5 5 6 5z" fill="#fff"/></svg>
        <span>+0000-0000-0000</span>
      </li>
      <li>
        <svg viewBox="0 0 20 20" aria-hidden="true"><rect width="20" height="20" rx="3" fill="#6fa9cc"/><rect x="4" y="6" width="12" height="8" fill="none" stroke="#fff" stroke-width="1.4"/><path d="M4 6l6 5 6-5" fill="none" stroke="#fff" stroke-width="1.4"/></svg>
        <span>info@yourdomain.com</span>
      </li>
      <li>
        <svg viewBox="0 0 20 20" aria-hidden="true"><rect width="20" height="20" rx="3" fill="#6fa9cc"/><circle cx="10" cy="10" r="5.5" fill="none" stroke="#fff" stroke-width="1.4"/><path d="M4.5 10h11M10 4.5c-2.5 3-2.5 8 0 11M10 4.5c2.5 3 2.5 8 0 11" fill="none" stroke="#fff" stroke-width="1.2"/></svg>
        <span>www.yourdomain.com</span>
      </li>
      <li>
        <svg viewBox="0 0 20 20" aria-hidden="true"><rect width="20" height="20" rx="3" fill="#6fa9cc"/><path d="M10 16s-4.5-4.5-4.5-7.5a4.5 4.5 0 0 1 9 0C14.5 11.5 10 16 10 16z" fill="#fff"/><circle cx="10" cy="8.5" r="1.6" fill="#6fa9cc"/></svg>
        <span>Studio 21,<br>8 Marlow Yard,<br>Kelbridge</span>
      </li>
    </ul>

    <div class="brand">
      <div class="brand-mark"></div>
      <p class="brand-name">Norvale<br>International</p>
    </div>
  </div>
</body>
</html>
```